Landing Page / Waitlist

I would like a landing page for people to sign up for a waiting list. The text on the page should include (but is not limited to):
1) Main point: The accounting system you'll love
2) Secondary points:
a. Ruthlessly efficient
b. Quietly intelligent
c. Driven by AI
I've attached a file of our logo

The design should be simple, clean, and innovative - this is an ai company

```html
<!DOCTYPE html>
<html lang="en">
<head>
<meta charset="utf-8">
<title>Evenledger — Waitlist Landing Page</title>
<link href="https://fonts.googleapis.com/css2?family=Poppins:ital,wght@0,400;0,500;0,600;1,400&display=swap" rel="stylesheet">
<style>
:root{
  --page:#ffffff;
  --ink:#04070b;
  --navy:#071827;
  --navy-line:#1d4f7c;
  --blue:#0a9bf5;
  --blue-deep:#0a6fcf;
  --white:#ffffff;
  --muted:#c9d3dc;
  --grey-text:#555b62;
  --dark-text:#111418;
  --client-bg:#f2f2f2;
  --logo-grey:#c7ccd1;
}
*{box-sizing:border-box;margin:0;padding:0}
html,body{width:1200px;height:2342px;overflow:hidden;background:var(--page)}
body{position:relative;font-family:"Poppins",sans-serif;color:var(--white)}
.abs{position:absolute}
.panel{position:absolute;width:516px;overflow:hidden}

/* shared hero */
.hero{background:radial-gradient(circle at 8% 0%,#0c3552 0%,rgba(4,7,11,0) 40%),linear-gradient(180deg,#050b12 0%,var(--ink) 100%)}
.brand{position:absolute;font-weight:500;color:var(--logo-grey);letter-spacing:-.2px;display:flex;align-items:center;gap:6px}
.brand .mark{display:inline-block;background:var(--blue)}
.btn{position:absolute;height:18px;border-radius:10px;font-size:6px;font-weight:500;display:flex;align-items:center;justify-content:center;gap:5px;color:var(--white)}
.btn svg{width:6px;height:6px}
.btn-solid{background:var(--blue)}
.btn-outline{border:1px solid var(--blue)}
.btn-white{background:var(--white);color:var(--dark-text)}
.hero-title{position:absolute;left:43px;top:130px;font-size:22px;font-weight:600;line-height:27px}
.hero-title .accent{color:var(--blue)}
.hero-sub{position:absolute;left:44px;top:193px;font-size:10px}
.hero-note{position:absolute;left:47px;top:265px;font-size:6.5px;font-style:italic;color:#7fb8e0}
.hero-visual{position:absolute;left:276px;top:72px;width:240px;height:273px;background:radial-gradient(ellipse at 55% 45%,#1b5f8f 0%,#0b2c47 40%,rgba(5,11,18,0) 75%)}
.feature{position:absolute;top:363px;width:140px}
.feature .icon{width:22px;height:22px;margin-left:2px}
.feature h3{font-size:8.5px;font-weight:500;margin-top:16px}
.feature p{font-size:6px;line-height:11px;margin-top:6px;color:var(--muted)}
.nav-pill{position:absolute;left:198px;top:20px;width:169px;height:25px;border:1px solid #263444;border-radius:13px;display:flex;align-items:center;padding-left:5px;gap:8px;font-size:5.6px}
.nav-pill .active{background:var(--blue);border-radius:9px;padding:3px 7px}
.foot-rule{position:absolute;left:54px;top:475px;width:430px;height:1px;background:#12324e}
.copyright{position:absolute;width:100%;text-align:center;font-size:5.5px}

/* about */
.about{background:var(--white);color:var(--dark-text)}
.about-mark{position:absolute;left:39px;top:56px;width:183px;height:232px;background:linear-gradient(135deg,#0a9bf5,#0a5fbf);display:flex;align-items:center;justify-content:center;font-size:22px;font-weight:500;color:var(--white)}
.about h2{position:absolute;left:257px;top:60px;font-size:17.5px;font-weight:600;line-height:23px}
.accent{color:var(--blue)}
.about .lead{position:absolute;left:257px;top:116px;width:225px;font-size:6px;line-height:11px;color:var(--grey-text)}
.about h4{position:absolute;left:257px;top:152px;font-size:9.5px;font-weight:500}
.ticks{position:absolute;left:257px;top:180px;width:225px;list-style:none;font-size:6px;line-height:11px;color:var(--grey-text)}
.ticks li{position:absolute;left:0;padding-left:12px;width:225px}
.ticks li::before{content:"";position:absolute;left:0;top:2.5px;width:6px;height:6px;border-radius:50%;background:var(--blue)}

/* how it works */
.how{background:radial-gradient(circle at 100% 50%,#0a2b47 0%,rgba(4,7,11,0) 45%),var(--ink)}
.section-title{position:absolute;width:100%;text-align:center;font-size:18px;font-weight:600}
.how .intro{position:absolute;left:106px;top:96px;width:304px;text-align:center;font-size:6px;line-height:11px}
.step-pill{position:absolute;width:90px;height:19px;border:1px solid var(--navy-line);background:#0b2a45;border-radius:10px;font-size:6px;font-weight:500;display:flex;align-items:center;justify-content:center}
.step-box{position:absolute;width:185px;height:65px;border:1px solid var(--navy-line);border-radius:3px;font-size:5.6px;line-height:11px;padding:0 14px;display:flex;align-items:center}
.step-box.right-text{text-align:right}
.wire{position:absolute;height:1px;background:var(--navy-line)}
.dot{position:absolute;width:5px;height:5px;border-radius:50%;background:var(--blue)}

/* testimonials */
.testimonials{background:var(--white);color:var(--dark-text)}
.quote{position:absolute;width:110px;font-size:5px;line-height:8.5px;color:var(--grey-text)}
.quote.featured{width:135px;height:107px;padding:10px 11px;background:var(--white);box-shadow:0 4px 14px rgba(0,0,0,.12);font-size:5.6px;line-height:10px}
.person{display:flex;align-items:center;gap:8px;margin-bottom:6px}
.avatar{width:26px;height:26px;border-radius:50%;background:radial-gradient(circle at 50% 40%,#6b7580,#2b3138)}
.featured .avatar{width:32px;height:32px}
.person b{display:block;font-size:5px;font-weight:600;color:var(--dark-text)}
.person span{font-size:4.5px}
.arrow-btn{position:absolute;border-radius:50%;display:flex;align-items:center;justify-content:center}

/* clients */
.clients{background:var(--client-bg);color:var(--dark-text)}
.client{position:absolute;top:70px;width:80px;margin-left:-40px;display:flex;flex-direction:column;align-items:center;gap:6px;font-size:7px;font-weight:600;color:#4a5058}
.client i{display:block;width:28px;height:28px;border-radius:4px;background:#9aa6b2}

/* call to action */
.cta{background:radial-gradient(circle at 20% 50%,#2a9cf2 0%,rgba(10,123,216,0) 45%),linear-gradient(90deg,#0a7fd8,#0b8ee6)}
.cta h2{position:absolute;width:100%;top:38px;text-align:center;font-size:17.5px;font-weight:600;line-height:24px}
.cta p{position:absolute;width:100%;top:96px;text-align:center;font-size:7.5px}

/* footer */
.footer{background:radial-gradient(ellipse at 0% 100%,#1d2630 0%,rgba(0,0,0,0) 40%),radial-gradient(ellipse at 100% 100%,#1d2630 0%,rgba(0,0,0,0) 40%),#000}
.foot-nav{position:absolute;top:92px;width:100%;display:flex;justify-content:center;gap:14px;font-size:6px}
.social{position:absolute;top:124px;width:17px;height:17px;border-radius:50%;background:var(--white)}
.social.on{background:var(--blue)}
</style>
</head>
<body>

<!-- compact hero -->
<section class="panel hero" style="left:55px;top:55px;height:514px">
  <div class="brand" style="left:60px;top:38px;font-size:16px"><span class="mark" style="width:12px;height:12px"></span>Evenledger</div>
  <a class="btn btn-solid" style="left:381px;top:33px;width:72px">Join Waitlist <svg viewBox="0 0 6 6"><path d="M1 5L5 1M2 1h3v3" stroke="#fff" fill="none" stroke-width=".8"/></svg></a>
  <div class="hero-visual" role="img" aria-label="Floating AI accounting dashboard with charts"></div>
  <h1 class="hero-title"><span class="accent">The Accounting system</span><br>you'll love</h1>
  <p class="hero-sub">Quiet intelligence built into every action.</p>
  <a class="btn btn-solid" style="left:45px;top:227px;width:72px">Join Waitlist <svg viewBox="0 0 6 6"><path d="M1 5L5 1M2 1h3v3" stroke="#fff" fill="none" stroke-width=".8"/></svg></a>
  <p class="hero-note">No spam. Just updates.</p>
  <div class="feature" style="left:49px"><svg class="icon" viewBox="0 0 22 22"><circle cx="11" cy="11" r="9" fill="none" stroke="#0a9bf5" stroke-width="1.2"/><circle cx="11" cy="11" r="4" fill="none" stroke="#0a9bf5"/></svg><h3>Quietly intelligent</h3><p>Learns your patterns, cleans your books, catches what humans miss.</p></div>
  <div class="feature" style="left:215px"><svg class="icon" viewBox="0 0 22 22"><circle cx="11" cy="11" r="9" fill="none" stroke="#0a9bf5" stroke-width="1.2"/><circle cx="11" cy="11" r="4" fill="none" stroke="#0a9bf5"/></svg><h3>Ruthlessly Efficient</h3><p>Automates the work you shouldn't be doing.</p></div>
  <div class="feature" style="left:363px"><svg class="icon" viewBox="0 0 22 22"><circle cx="11" cy="11" r="9" fill="none" stroke="#0a9bf5" stroke-width="1.2"/><circle cx="11" cy="11" r="4" fill="none" stroke="#0a9bf5"/></svg><h3>Driven by AI</h3><p>Always improving, always watching your financial blind spots.</p></div>
  <div class="foot-rule"></div>
  <p class="copyright" style="top:488px">Copyright@2025.All Rights Reserved.</p>
</section>

<!-- full landing page: hero -->
<section class="panel hero" style="left:617px;top:55px;height:485px">
  <div class="brand" style="left:61px;top:26px;font-size:13px"><span class="mark" style="width:10px;height:10px"></span>Evenledger</div>
  <nav class="nav-pill"><span class="active">Home</span><span>How It Works</span><span>Features</span><span>Pricing</span></nav>
  <a class="btn btn-solid" style="left:380px;top:24px;width:72px">Join Waitlist <svg viewBox="0 0 6 6"><path d="M1 5L5 1M2 1h3v3" stroke="#fff" fill="none" stroke-width=".8"/></svg></a>
  <div class="hero-visual" role="img" aria-label="Floating AI accounting dashboard with charts"></div>
  <h1 class="hero-title"><span class="accent">The Accounting system</span><br>you'll love</h1>
  <p class="hero-sub">Quiet intelligence built into every action.</p>
  <a class="btn btn-solid" style="left:45px;top:227px;width:72px">Join Waitlist <svg viewBox="0 0 6 6"><path d="M1 5L5 1M2 1h3v3" stroke="#fff" fill="none" stroke-width=".8"/></svg></a>
  <a class="btn btn-outline" style="left:124px;top:227px;width:90px">Get Early Access <svg viewBox="0 0 6 6"><path d="M1 5L5 1M2 1h3v3" stroke="#0a9bf5" fill="none" stroke-width=".8"/></svg></a>
  <p class="hero-note">No spam. Just updates.</p>
  <div class="feature" style="left:49px"><svg class="icon" viewBox="0 0 22 22"><circle cx="11" cy="11" r="9" fill="none" stroke="#0a9bf5" stroke-width="1.2"/><circle cx="11" cy="11" r="4" fill="none" stroke="#0a9bf5"/></svg><h3>Quietly intelligent</h3><p>Learns your patterns, cleans your books, catches what humans miss.</p></div>
  <div class="feature" style="left:215px"><svg class="icon" viewBox="0 0 22 22"><circle cx="11" cy="11" r="9" fill="none" stroke="#0a9bf5" stroke-width="1.2"/><circle cx="11" cy="11" r="4" fill="none" stroke="#0a9bf5"/></svg><h3>Ruthlessly Efficient</h3><p>Automates the work you shouldn't be doing.</p></div>
  <div class="feature" style="left:363px"><svg class="icon" viewBox="0 0 22 22"><circle cx="11" cy="11" r="9" fill="none" stroke="#0a9bf5" stroke-width="1.2"/><circle cx="11" cy="11" r="4" fill="none" stroke="#0a9bf5"/></svg><h3>Driven by AI</h3><p>Always improving, always watching your financial blind spots.</p></div>
</section>

<!-- about -->
<section class="panel about" style="left:617px;top:540px;height:333px">
  <div class="about-mark">Evenledger</div>
  <h2><span class="accent">A New Era</span> of Accounting<br>Starts Here</h2>
  <p class="lead">No clutter. No confusion. No emotional damage from spreadsheets. Just a system that anticipates, organizes, and simplifies your financial life.</p>
  <h4>What makes us different?</h4>
  <ul class="ticks">
    <li style="top:0">It reads your financial world, not just records it.</li>
    <li style="top:22px">It adapts to your business as you grow.</li>
    <li style="top:44px">It saves hours each week with automated reconciliation and insight generation.</li>
    <li style="top:77px">It quietly removes mistakes before they become expensive.</li>
  </ul>
</section>

<!-- how it works -->
<section class="panel how" style="left:617px;top:884px;height:551px">
  <h2 class="section-title" style="top:58px"><span class="accent">How</span> It Works</h2>
  <p class="intro">Lorem ipsum dolor sit amet, consectetur adipiscing elit, sed do eiusmod tempor incididunt ut labore et dolore magna aliqua. Ut enim ad minim veniam, quis nostrud exercitation ullamco laboris nisi ut aliquip ex ea commodo consequat.</p>

  <div class="step-pill" style="left:106px;top:177px">Connect With Us</div>
  <div class="wire" style="left:196px;top:186px;width:56px"></div><div class="dot" style="left:250px;top:184px"></div>
  <div class="step-box" style="left:252px;top:154px">Lorem ipsum dolor sit amet, consectetur adipiscing elit, sed do eiusmod tempor incididunt ut labore et dolore magna aliqua.</div>

  <div class="step-box right-text" style="left:96px;top:243px">Lorem ipsum dolor sit amet, consectetur adipiscing elit, sed do eiusmod tempor incididunt ut labore et dolore magna aliqua.</div>
  <div class="wire" style="left:278px;top:276px;width:56px"></div><div class="dot" style="left:276px;top:274px"></div>
  <div class="step-pill" style="left:334px;top:267px">Watch it learn</div>

  <div class="step-pill" style="left:106px;top:354px">Automate everything</div>
  <div class="wire" style="left:196px;top:363px;width:56px"></div><div class="dot" style="left:250px;top:361px"></div>
  <div class="step-box" style="left:252px;top:330px">Lorem ipsum dolor sit amet, consectetur adipiscing elit, sed do eiusmod tempor incididunt ut labore et dolore magna aliqua.</div>

  <div class="step-box right-text" style="left:96px;top:419px">Lorem ipsum dolor sit amet, consectetur adipiscing elit, sed do eiusmod tempor incididunt ut labore et dolore magna aliqua.</div>
  <div class="wire" style="left:278px;top:453px;width:56px"></div><div class="dot" style="left:276px;top:451px"></div>
  <div class="step-pill" style="left:334px;top:444px">Make better decisions</div>
</section>

<!-- testimonials -->
<section class="panel testimonials" style="left:617px;top:1435px;height:254px">
  <h2 class="section-title" style="top:48px"><span class="accent">Our</span> Testimonials</h2>
  <div class="arrow-btn" style="left:30px;top:135px;width:23px;height:23px;box-shadow:0 1px 6px rgba(0,0,0,.15)"><svg width="7" height="7" viewBox="0 0 7 7"><path d="M3.5 1L1 3.5 3.5 6M6 1L3.5 3.5 6 6" stroke="#333" fill="none"/></svg></div>
  <div class="quote" style="left:71px;top:103px"><div class="person"><div class="avatar" role="img" aria-label="Customer portrait"></div><div><b>MARA QUILL</b><span>Lorum Ipsum City</span></div></div>Lorem ipsum dolor sit amet, consectetur adipisc ing elit, sed do eiusmod tempor incididunt ut labore et dolore magna aliqua. Ut enim ad minim veniam, quis nostrud</div>
  <div class="quote featured" style="left:190px;top:93px"><div class="person"><div class="avatar" role="img" aria-label="Customer portrait"></div><div><b>MARA QUILL</b><span>Lorum Ipsum City</span></div></div>Lorem ipsum dolor sit amet, consectetur adipisc ing elit, sed do eiusmod tempor incididunt ut labore et dolore magna aliqua. Ut enim ad minim veniam, quis nostrud</div>
  <div class="quote" style="left:346px;top:103px"><div class="person"><div class="avatar" role="img" aria-label="Customer portrait"></div><div><b>MARA QUILL</b><span>Lorum Ipsum City</span></div></div>Lorem ipsum dolor sit amet, consectetur adipisc ing elit, sed do eiusmod tempor incididunt ut labore et dolore magna aliqua. Ut enim ad minim veniam, quis nostrud</div>
  <div class="arrow-btn" style="left:465px;top:136px;width:20px;height:20px;background:var(--blue)"><svg width="7" height="7" viewBox="0 0 7 7"><path d="M3.5 1L6 3.5 3.5 6M1 1l2.5 2.5L1 6" stroke="#fff" fill="none"/></svg></div>
</section>

<!-- clients -->
<section class="panel clients" style="left:617px;top:1689px;height:172px">
  <h2 class="section-title" style="top:33px"><span class="accent">Our</span> Clients</h2>
  <div class="client" style="left:89px"><i></i>Northpeak</div>
  <div class="client" style="left:172px"><i></i>Linkfold</div>
  <div class="client" style="left:255px"><i></i>Emberly</div>
  <div class="client" style="left:338px"><i></i>Orbitra</div>
  <div class="client" style="left:422px"><i></i>Boxwell</div>
</section>

<!-- call to action -->
<section class="panel cta" style="left:617px;top:1861px;height:200px">
  <h2>Be First to Experience<br>The Future of Accounting</h2>
  <p>Join the early user group and shape the product as it evolves.</p>
  <a class="btn btn-white" style="left:213px;top:125px;width:90px">Join Our Waitlist <svg viewBox="0 0 6 6"><path d="M1 5L5 1M2 1h3v3" stroke="#0a9bf5" fill="none" stroke-width=".8"/></svg></a>
</section>

<!-- footer -->
<footer class="panel footer" style="left:617px;top:2061px;height:215px">
  <div class="brand" style="left:0;width:516px;justify-content:center;top:60px;font-size:13px"><span class="mark" style="width:10px;height:10px"></span>Evenledger</div>
  <nav class="foot-nav"><span>Home</span><span>How It Works</span><span>Features</span><span>Pricing</span><span>Contact Us</span></nav>
  <span class="social" style="left:237px" aria-label="Social link"></span>
  <span class="social on" style="left:258px" aria-label="Social link"></span>
  <span class="social" style="left:279px" aria-label="Social link"></span>
  <p class="copyright" style="top:151px">Copyright@2025.All Rights Reserved.</p>
</footer>

</body>
</html>
```